Web Site Design For Real Estate Sales Project

The idea behind this project is pretty simple. I am putting my penthouse apartment up for sale and am trying to be creative in selling it.
Technically this will be pretty simple, it will be 3 pages but graphically this has to be as impressive as possible which is why I am trying Pixel Harbor.
The apartment is located in Barra Da Tijuca, Rio De Janeiro, Brazil. (This is where the 2016 Solstice Meet will be held)
I am looking for an index page and 2 sub-pages. I am open to all kinds of designs and navigation's but it has to make an impression quickly with a professional and enticing design. The index page should make it obvious that there is a penthouse apartment for sale in Barra Da Tijuca ( suburb of Rio De Janeiro). The first sub page is about the Condominium where the apartment is located, the second sub page is about the apartment itself.
Here is a more detailed description of what the 3 pages should be about.
Index Page
This is the landing page and should make it obvious that there is an apartment for sale in Barra Da Tijuca, Rio De Janeiro with the following attributes
251 SQ M
Duplex Penthouse
4 suites
Price R$ 2.200.000
Price per SQ M: R$ 8.764
First Sub-Page
This is about the Condominium which is called "Tranquil Cliff Suites" with the following bullets
*Family friendly and safe
*Direct access to the beach
*Many amenities like pool, football court, gym, sauna
There should be some photos of the condominium and a link to the site of the condominium ( www.tcsqv.com )
Second Sub-page
This is about the apartment. It should list in bullets the features of the apartment and then have a photo gallery of the view and various rooms. I have attached sample photos but will eventually have to use more photos.
Apartment Features
Price: R$ 2.220.000
251 m2 Duplex Penthouse
4 suites
maids room with bath
guest bathroom
living room
dinning room
Terrace with heated pool for year round use
Veranda
As mentioned above I am open to all designs and navigation so feel free to be creative. The important thing is catch peoples attention and get the message across in a few seconds, which is that there is an apartment for sale at this price with these features in this location. I will then use zintra clickreach and SEO to get people to the site.
Thanks
Men and Women from 30-60 years of age.
Apartment

```html
<!DOCTYPE html>
<html lang="en">
<head>
<meta charset="utf-8">
<title>Penthouse Sale</title>
<link href="https://fonts.googleapis.com/css2?family=Ubuntu:wght@300;400;500&family=Noto+Serif:ital@0;1&display=swap" rel="stylesheet">
<style>
:root{
  --ink:#2b2b2b;
  --muted:#666;
  --orange:#f7941d;
  --orange-dark:#e57f0a;
  --bar:#2e2e2e;
  --panel:#efefef;
  --line:#d6d6d6;
  --footer:#1f1f1f;
  --footer-text:#cfcfcf;
  --white:#fff;
}
*{box-sizing:border-box;margin:0;padding:0}
html,body{width:720px;height:1200px;overflow:hidden}
body{position:relative;font-family:"Ubuntu",sans-serif;color:var(--ink);background:var(--white)}
a{color:inherit;text-decoration:none}
.abs{position:absolute}

.top-bar{left:0;top:0;width:720px;height:30px;background:linear-gradient(#3a3a3a,#242424)}
.top-links{right:78px;top:10px;font-size:7.5px;color:#bbb}
.top-links span{margin:0 3px;color:#777}

.site-header{left:0;top:30px;width:720px;height:58px;background:var(--white)}
.logo{left:77px;top:20px;font-size:20px;font-weight:500;color:var(--ink);letter-spacing:.3px}
.main-nav{left:270px;top:27px;font-size:7.8px;color:#333}
.main-nav span{margin:0 6px;color:#777}
.search{left:510px;top:19px;width:132px;height:23px;border:1px solid #ccc;border-radius:2px;background:#f6f6f6}
.search em{position:absolute;left:8px;top:7px;font-size:7px;color:#aaa}
.search svg{position:absolute;right:4px;top:3px}

.hero-rule{left:0;top:88px;width:720px;height:16px;background:linear-gradient(#fff,#eaeaea)}
.hero{left:0;top:104px;width:720px;height:270px;background:linear-gradient(100deg,#6d6c66 0%,#8a8577 35%,#cfc6ac 55%,#6f8e94 70%,#3f6c7e 100%)}
.hero-arrow{top:106px;width:47px;height:59px;background:rgba(230,230,230,.55)}
.hero-arrow.left{left:0}
.hero-arrow.right{right:0}
.hero-arrow svg{position:absolute;left:16px;top:20px}
.hero-info{left:414px;top:71px;width:228px;height:128px;background:rgba(40,40,40,.85);padding:10px 11px;color:var(--white)}
.hero-info h1{font-size:20px;font-weight:500;letter-spacing:.3px}
.hero-info p{font-size:14px;font-weight:300;margin-top:3px}
.hero-info .price{color:var(--orange);font-size:15px;font-weight:400}
.hero-info .per{font-size:8px;font-style:italic;color:#ddd;margin-top:6px}

.section-title{font-size:16px;font-weight:400;color:var(--ink);letter-spacing:.2px}
.all-sales{font-size:9.5px;color:#777}
.all-sales svg{vertical-align:middle;margin-left:3px}

.card{background:var(--white);border:1px solid var(--line)}
.card.tinted{background:var(--panel)}
.photo{position:absolute;left:0;top:0;width:100%}
.card h3{position:absolute;width:100%;text-align:center;font-size:9px;font-weight:400;color:var(--ink)}
.card .desc{position:absolute;width:100%;text-align:center;font-size:7px;color:#555;line-height:1.55}
.card .rule{position:absolute;left:8px;right:8px;border-top:1px dashed #bbb}
.read-more{position:absolute;left:9px;font-family:"Noto Serif",serif;font-style:italic;font-size:8.5px;color:#444}
.go{position:absolute;right:7px;width:19px;height:19px;border-radius:50%;background:var(--orange)}
.go svg{position:absolute;left:4px;top:4px}

.feature-text{position:absolute;left:9px;top:164px;width:258px}
.feature-text h2{font-size:11.5px;font-weight:400}
.feature-text .spec{font-size:7.5px;font-style:italic;color:#555;line-height:1.6;margin-top:2px}
.feature-text .body{font-size:7px;color:#555;line-height:1.9;margin-top:3px}
.feature-price{position:absolute;left:9px;top:253px;font-family:"Noto Serif",serif;font-size:14px;letter-spacing:.4px}

.suites-band{left:0;top:718px;width:720px;height:291px;background:var(--panel)}
.to-top{left:682px;top:970px;width:30px;height:30px;border-radius:4px;background:#8a8a8a}
.to-top svg{position:absolute;left:7px;top:8px}

.site-footer{left:0;top:1009px;width:720px;height:191px;background:var(--footer);color:var(--footer-text)}
.footer-logo{left:77px;top:22px;font-size:17px;font-weight:400;color:var(--white)}
.footer-col{top:57px;border-top:1px solid #444;padding-top:12px;width:132px;font-size:7.8px;line-height:18.5px}
.footer-col li{list-style:none}
.social li{display:flex;align-items:center}
.social i{display:inline-block;width:9px;height:9px;border-radius:1px;margin-right:9px}
.footer-bottom{left:78px;top:151px;width:564px;border-top:1px solid #444}
.copyright{left:78px;top:163px;font-size:7.2px;color:#aaa}
.copyright span{margin:0 4px}
.phone{right:78px;top:156px;font-family:"Noto Serif",serif;font-size:14px;color:var(--white);display:flex;align-items:center}
.phone svg{margin-right:9px}
</style>
</head>
<body>

<svg width="0" height="0" style="position:absolute">
  <defs>
    <symbol id="arrow-white" viewBox="0 0 11 11"><path d="M1 5.5h8M6 2.5l3 3-3 3" stroke="#fff" stroke-width="1.2" fill="none"/></symbol>
  </defs>
</svg>

<div class="abs top-bar">
  <nav class="abs top-links"><a href="#">Contact Us</a><span>|</span><a href="#">Register</a><span>|</span><a href="#">Login</a><span>|</span><a href="#">Site Map</a></nav>
</div>

<header class="abs site-header">
  <div class="abs logo">Penthouse Sale</div>
  <nav class="abs main-nav"><a href="#">Home</a><span>|</span><a href="#">Tranquil Cliff Suites</a><span>|</span><a href="#">The Apartment</a></nav>
  <div class="abs search"><em>Search Keyword.....</em>
    <svg width="18" height="16" viewBox="0 0 18 16"><circle cx="7" cy="6.5" r="4.5" stroke="#222" stroke-width="2" fill="none"/><path d="M10.5 9.5l5 4.5" stroke="#222" stroke-width="2.4" stroke-linecap="round"/></svg>
  </div>
</header>

<div class="abs hero-rule"></div>
<section class="abs hero" role="img" aria-label="Aerial photo of the beachfront towers and coastline of Barra da Tijuca">
  <div class="abs hero-arrow left"><svg width="14" height="20" viewBox="0 0 14 20"><path d="M11 2L3 10l8 8" stroke="#fff" stroke-width="1.5" fill="none"/></svg></div>
  <div class="abs hero-arrow right"><svg width="14" height="20" viewBox="0 0 14 20"><path d="M3 2l8 8-8 8" stroke="#fff" stroke-width="1.5" fill="none"/></svg></div>
  <div class="abs hero-info">
    <h1>Duplex Penthouse</h1>
    <p>251 SQ M</p>
    <p>4 suites</p>
    <p class="price">Price R$ 2.200.000</p>
    <p class="per">Price per SQ M: R$ 8.764</p>
  </div>
</section>

<h2 class="abs section-title" style="left:77px;top:396px">Featured Penthouse</h2>
<a class="abs all-sales" href="#" style="left:585px;top:399px">All Sales<svg width="16" height="10" viewBox="0 0 16 10"><path d="M1 5h13M10 1l4 4-4 4" stroke="#ccc" stroke-width="1.3" fill="none"/></svg></a>

<article class="abs card tinted" style="left:78px;top:424px;width:276px;height:280px">
  <div class="photo" role="img" aria-label="Penthouse living room with wooden floor and staircase" style="height:158px;background:linear-gradient(110deg,#d8d2c4,#9a7a5c 50%,#4a3a30)"></div>
  <div class="feature-text">
    <h2>Duplex Heading Goes Here !</h2>
    <p class="spec">251 SQ M<br>4 suites<br><b style="font-weight:500">Price per SQ M: R$ 8.764</b></p>
    <p class="body">Lorem ipsum dolor sit amet, consectetur adipisicing eitseo eiusmod<br>tempor incididunt ut labore et dolore magna aliqua.</p>
  </div>
  <div class="rule" style="top:250px"></div>
  <div class="feature-price">R$ 2.200.000</div>
  <div class="go" style="top:258px"><svg width="11" height="11"><use href="#arrow-white"/></svg></div>
</article>

<article class="abs card tinted" style="left:366px;top:424px;width:132px;height:134px">
  <div class="photo" role="img" aria-label="Open-plan room with hallway" style="height:75px;background:linear-gradient(120deg,#cfc6b8,#7d6a5a)"></div>
  <h3 style="top:80px">Heading Goes Here !</h3>
  <p class="desc" style="top:92px">Lorem ipsum dolor sit amet...</p>
  <div class="rule" style="top:105px"></div>
  <span class="read-more" style="top:116px">Read More</span>
  <div class="go" style="top:112px"><svg width="11" height="11"><use href="#arrow-white"/></svg></div>
</article>
<article class="abs card tinted" style="left:511px;top:424px;width:132px;height:134px">
  <div class="photo" role="img" aria-label="Rooftop terrace with pool and loungers" style="height:75px;background:linear-gradient(120deg,#3a3a3a,#8c3b34 55%,#5fb5d0)"></div>
  <h3 style="top:80px">Heading Goes Here !</h3>
  <p class="desc" style="top:92px">Lorem ipsum dolor sit amet...</p>
  <div class="rule" style="top:105px"></div>
  <span class="read-more" style="top:116px">Read More</span>
  <div class="go" style="top:112px"><svg width="11" height="11"><use href="#arrow-white"/></svg></div>
</article>
<article class="abs card tinted" style="left:366px;top:569px;width:132px;height:135px">
  <div class="photo" role="img" aria-label="Terrace with barbecue area and planters" style="height:75px;background:linear-gradient(170deg,#c9d6de,#9a8f86 55%,#5a4a44)"></div>
  <h3 style="top:80px">Heading Goes Here !</h3>
  <p class="desc" style="top:92px">Lorem ipsum dolor sit amet...</p>
  <div class="rule" style="top:105px"></div>
  <span class="read-more" style="top:116px">Read More</span>
  <div class="go" style="top:112px"><svg width="11" height="11"><use href="#arrow-white"/></svg></div>
</article>
<article class="abs card tinted" style="left:511px;top:569px;width:132px;height:135px">
  <div class="photo" role="img" aria-label="Veranda view over towers and hills" style="height:75px;background:linear-gradient(170deg,#b9cbd8,#8d8f7a 50%,#4e5a3c)"></div>
  <h3 style="top:80px">Heading Goes Here !</h3>
  <p class="desc" style="top:92px">Lorem ipsum dolor sit amet...</p>
  <div class="rule" style="top:105px"></div>
  <span class="read-more" style="top:116px">Read More</span>
  <div class="go" style="top:112px"><svg width="11" height="11"><use href="#arrow-white"/></svg></div>
</article>

<div class="abs suites-band"></div>
<h2 class="abs section-title" style="left:77px;top:731px">Tranquil Cliff Suites</h2>
<a class="abs all-sales" href="#" style="left:585px;top:734px">All Sales<svg width="16" height="10" viewBox="0 0 16 10"><path d="M1 5h13M10 1l4 4-4 4" stroke="#ccc" stroke-width="1.3" fill="none"/></svg></a>

<article class="abs card" style="left:78px;top:760px;width:132px;height:237px">
  <div class="photo" role="img" aria-label="Poolside tables under parasols" style="height:149px;background:linear-gradient(170deg,#e6e8ea,#a9aca6 55%,#6c7060)"></div>
  <h3 style="top:162px">Heading Goes Here !</h3>
  <p class="desc" style="top:174px">Lorem ipsum dolor sit amet<br>consectetur adipisicing eitseo<br>eiusmod tempor</p>
  <div class="rule" style="top:207px"></div>
  <span class="read-more" style="top:218px">Read More</span>
  <div class="go" style="top:214px"><svg width="11" height="11"><use href="#arrow-white"/></svg></div>
</article>
<article class="abs card" style="left:222px;top:760px;width:132px;height:237px">
  <div class="photo" role="img" aria-label="Condominium pool deck with tables" style="height:149px;background:linear-gradient(170deg,#6f7a4a,#5aa4c0 40%,#a8926a)"></div>
  <h3 style="top:162px">Heading Goes Here !</h3>
  <p class="desc" style="top:174px">Lorem ipsum dolor sit amet<br>consectetur adipisicing eitseo<br>eiusmod tempor</p>
  <div class="rule" style="top:207px"></div>
  <span class="read-more" style="top:218px">Read More</span>
  <div class="go" style="top:214px"><svg width="11" height="11"><use href="#arrow-white"/></svg></div>
</article>
<article class="abs card" style="left:366px;top:760px;width:277px;height:237px">
  <div class="photo" role="img" aria-label="Condominium entrance and driveway" style="height:150px;background:linear-gradient(160deg,#a4b4c4,#8c6a58 40%,#9a9a98)"></div>
  <h3 style="top:163px;left:9px;text-align:left;font-size:11px">Heading Goes Here !</h3>
  <p class="desc" style="top:178px;left:9px;text-align:left;line-height:1.9">Lorem ipsum dolor sit amet, consectetur adipisicing eitseo eiusmod<br>tempor incididunt ut labore et dolore magna aliqua.</p>
  <div class="rule" style="top:207px"></div>
  <span class="read-more" style="top:216px">Read More</span>
  <div class="go" style="top:213px"><svg width="11" height="11"><use href="#arrow-white"/></svg></div>
</article>

<a class="abs to-top" href="#" aria-label="Back to top"><svg width="16" height="12" viewBox="0 0 16 12"><path d="M1 11l7-9 7 9" stroke="#fff" stroke-width="1.5" fill="none"/></svg></a>

<footer class="abs site-footer">
  <div class="abs footer-logo">Penthouse Sale</div>
  <ul class="abs footer-col" style="left:78px"><li>Home</li><li>Tranquil Cliff Suites</li><li>The Apartment</li></ul>
  <ul class="abs footer-col" style="left:222px"><li>Contact Us</li><li>Terms of Services</li><li>Privacy Policy</li></ul>
  <ul class="abs footer-col" style="left:365px"><li>Login</li><li>Register</li><li>Newsletter SignUp</li></ul>
  <ul class="abs footer-col social" style="left:510px"><li><i style="background:#3b5998"></i>Friendnest</li><li><i style="background:#2fa8d8"></i>Chirpline</li><li><i style="background:#2a6fa8"></i>Workweb</li><li><i style="background:#f28a1c"></i>Rss Feed</li></ul>
  <div class="abs footer-bottom"></div>
  <p class="abs copyright">© 2013. All Right Reserved<span>|</span>Privacy Policy</p>
  <div class="abs phone"><svg width="17" height="17" viewBox="0 0 17 17"><circle cx="8.5" cy="8.5" r="8.5" fill="#777"/><path d="M5.5 4.5c-.8.6-1 1.8.3 3.8s2.8 3.6 4.6 4.2c1 .3 1.8-.2 2.1-.9l-1.6-1.4-1 .6c-.9-.4-1.9-1.5-2.4-2.5l.7-.9L6.9 4.4z" fill="#fff"/></svg>123 456 7890</div>
</footer>

</body>
</html>
```